Request for Business Card Design

Hi. My name is Marlene, I am looking for a new business card design for my company, Quarrow Signal Instruments, LLC. I really like the design you did for Tarsel Venture and was hoping you could do something similar using our full logo and our mark. I am also open to any raised texture design using our mark. I have attached our full logo, which would need to be somewhere on the card, as well as the mark in both outline and full form, as well as our brand colors / guide. The card does not have to be white, as long as our logo and mark appear. I actually like darker colored business cards more, but am open to all options. If you are interested in working with me, please let me know. We would also take the business card design into letterhead design if you can do that.

```html
<!DOCTYPE html>
<html lang="en">
<head>
<meta charset="utf-8">
<title>Quarrow Signal Instruments – Business Card</title>
<link href="https://fonts.googleapis.com/css2?family=Open+Sans:wght@400;600;700&display=swap" rel="stylesheet">
<style>
  :root {
    --page: #e6e3df;
    --card: #1f2024;
    --card-deep: #141518;
    --brand-blue: #1a9dc8;
    --logo-grey: #55575c;
    --text-light: #f1f1f1;
    --shadow: rgba(0,0,0,0.28);
  }
  html, body {
    margin: 0;
    width: 1200px;
    height: 780px;
    overflow: hidden;
    background: var(--page);
    font-family: "Open Sans", Arial, sans-serif;
  }
  .canvas {
    position: relative;
    width: 1200px;
    height: 780px;
  }
  .card {
    position: absolute;
    top: 225px;
    width: 540px;
    height: 310px;
    background: var(--card);
    border-radius: 4px;
    box-shadow: 0 12px 30px var(--shadow);
    overflow: hidden;
  }
  .card--front { left: 45px; }
  .card--back  { left: 615px; }

  /* Front */
  .brand {
    position: absolute;
    left: 26px;
    top: 22px;
    display: flex;
    align-items: center;
    gap: 12px;
  }
  .brand__dot {
    width: 34px;
    height: 34px;
    border-radius: 50%;
    background: var(--brand-blue);
  }
  .brand__name {
    font-weight: 700;
    color: var(--logo-grey);
    font-size: 30px;
    letter-spacing: 3px;
    line-height: 1;
  }
  .brand__tagline {
    display: block;
    font-size: 8.5px;
    letter-spacing: 1.2px;
    margin-top: 5px;
    font-weight: 700;
  }
  .address {
    position: absolute;
    left: 30px;
    top: 96px;
    margin: 0;
    color: var(--text-light);
    font-size: 14px;
    line-height: 20px;
    font-style: normal;
  }
  .contacts {
    position: absolute;
    left: 30px;
    top: 150px;
    margin: 0;
    padding: 0;
    list-style: none;
    color: var(--text-light);
    font-size: 14px;
    line-height: 21px;
  }
  .contacts li { display: flex; align-items: center; gap: 8px; }
  .contacts svg { width: 12px; height: 12px; flex: none; }
  .raised-mark {
    position: absolute;
    right: 60px;
    bottom: -40px;
    width: 250px;
    height: 250px;
    border-radius: 50%;
    background: radial-gradient(circle at 70% 30%, #3a3b40 0%, #17181b 55%, #101113 100%);
  }
  .person {
    position: absolute;
    right: 34px;
    top: 36px;
    text-align: right;
  }
  .person__name {
    margin: 0;
    color: var(--brand-blue);
    font-weight: 700;
    font-size: 34px;
    line-height: 1;
  }
  .person__role {
    margin: 4px 0 0;
    color: var(--text-light);
    font-size: 15px;
  }
  .edge-tab {
    position: absolute;
    right: 0;
    top: 32px;
    width: 12px;
    height: 62px;
    background: var(--brand-blue);
  }

  /* Back */
  .texture {
    position: absolute;
    inset: 0;
    background: linear-gradient(100deg, #141518 0%, #1a1b1e 55%, #4a4c52 85%, #9a9ca1 100%);
  }
  .brand--small {
    left: auto;
    top: auto;
    right: 120px;
    bottom: 40px;
    gap: 8px;
    background: var(--card-deep);
    padding: 6px 10px;
  }
  .brand--small .brand__dot { width: 18px; height: 18px; }
  .brand--small .brand__name { font-size: 15px; letter-spacing: 1.5px; }
  .brand--small .brand__tagline { font-size: 5px; margin-top: 2px; letter-spacing: 0.6px; }
</style>
</head>
<body>
<main class="canvas">

  <section class="card card--front" aria-label="Business card front">
    <div class="brand">
      <span class="brand__dot"></span>
      <span class="brand__name">QUARROW<span class="brand__tagline">SIGNAL INSTRUMENTS</span></span>
    </div>

    <address class="address">1180 Harlow Mill Road<br>Brenford, CO 80611</address>

    <ul class="contacts">
      <li>
        <svg viewBox="0 0 12 12"><path d="M2 1l2 0 1 3-1.5 1a6 6 0 0 0 3 3L7.5 7l3 1v2a1 1 0 0 1-1 1A9 9 0 0 1 1 2a1 1 0 0 1 1-1z" fill="var(--brand-blue)"/></svg>
        +001 555 218 4402
      </li>
      <li>
        <svg viewBox="0 0 12 12"><rect x="1" y="4" width="10" height="7" rx="1" fill="var(--brand-blue)"/><rect x="3" y="1" width="6" height="3" fill="var(--brand-blue)"/></svg>
        +001 555 218 4417
      </li>
      <li>
        <svg viewBox="0 0 12 12"><circle cx="6" cy="6" r="5" fill="none" stroke="var(--brand-blue)" stroke-width="1.3"/><path d="M1 6h10M6 1c-3 3-3 7 0 10M6 1c3 3 3 7 0 10" fill="none" stroke="var(--brand-blue)" stroke-width="1"/></svg>
        www.quarrowsignal.com
      </li>
      <li>
        <svg viewBox="0 0 12 12"><rect x="1" y="2.5" width="10" height="7" rx="1" fill="var(--brand-blue)"/><path d="M1.5 3l4.5 3.5L10.5 3" fill="none" stroke="var(--card)" stroke-width="1"/></svg>
        info@quarrowsignal.com
      </li>
    </ul>

    <div class="raised-mark" role="img" aria-label="Large raised brand mark in dark embossed finish"></div>

    <div class="person">
      <p class="person__name">Marlene</p>
      <p class="person__role">Director</p>
    </div>
    <span class="edge-tab"></span>
  </section>

  <section class="card card--back" aria-label="Business card back">
    <div class="texture" role="img" aria-label="Repeating raised brand mark pattern with a glossy highlight toward the right edge"></div>
    <div class="brand brand--small">
      <span class="brand__dot"></span>
      <span class="brand__name">QUARROW<span class="brand__tagline">SIGNAL INSTRUMENTS</span></span>
    </div>
  </section>

</main>
</body>
</html>
```